A Modern & Sleek "Coming Soon" Page for an A.I Recruiting App

For the “Coming Soon” website, a simple background with no people in it. I've attached an A.I image of what the page should generally look like.

- A single mobile phone as the main focus where the user actually clicks on the, “notify me” button (after entering their email address).
- In the background where the pillars/columns are seen in the example, should be subtle pad locks that are in their opened position with a key inside the lock. I've attached images to try to illustrate this idea, but they are far away in style from what I'm looking for.

SLOGAN: Unlocking the power of meaningful connections
LOGO/TITLE: Should be the name as shown in image with only the name "KelvoLink" on it
COLORS: Purplish/blue hues. Should not be too feminine
NOTE: The user should only click once when signing up/entering their email.

Product: A recruiting platform that matches employers/employees with A.I. and prioritizing cultural fit/values system before skills. The industry we are tackling first is the caregiving industry (nannies, tutors, elderly). All users will be background screened and that info lives on the blockchain. All users will have the option to review and be reviewed/rated.

```html
<!DOCTYPE html>
<html lang="en">
<head>
<meta charset="utf-8">
<title>KelvoLink — Coming Soon</title>
<link href="https://fonts.googleapis.com/css2?family=Jost:wght@300;400;500;600;700;800&display=swap" rel="stylesheet">
<style>
  :root{
    --white:#ffffff;
    --ink:#2a2a2a;
    --body:#6a6a6a;
    --magenta:#b0268e;
    --violet:#4a12b4;
    --logo:#4b18b8;
    --footer:#2a2a2a;
  }
  *{margin:0;padding:0;box-sizing:border-box}
  html,body{width:1200px;height:902px;overflow:hidden;background:var(--white)}
  body{font-family:"Jost",sans-serif;position:relative}
  .page{position:relative;width:1200px;height:902px;overflow:hidden;background:var(--white)}
  .backdrop{position:absolute;left:0;top:0;width:1200px;height:842px}
  .brand{position:absolute;left:112px;top:50px;font-family:"Jost",sans-serif;font-weight:300;font-size:50px;letter-spacing:6px;color:var(--logo);line-height:1}
  .menu-icon{position:absolute;left:1087px;top:41px}
  .headline{position:absolute;left:110px;top:169px;color:var(--ink);font-weight:700;text-transform:uppercase;line-height:1;-webkit-text-stroke:2px var(--white);paint-order:stroke fill;white-space:nowrap}
  .headline span{display:block}
  .headline .l1{font-size:90px;line-height:90px;letter-spacing:-1px;margin-bottom:24px}
  .headline .l2,.headline .l3,.headline .l4{font-size:69px;line-height:69px}
  .headline .l2,.headline .l3{margin-bottom:28px}
  .intro{position:absolute;left:112px;top:573px;width:552px;font-size:17.6px;line-height:33px;color:var(--body);font-weight:400}
  .actions{position:absolute;left:112px;top:700px;display:flex;gap:15px}
  .btn{width:135px;height:40px;border-radius:20px;color:var(--white);font-weight:600;font-size:14px;display:flex;align-items:center;justify-content:center}
  .btn-notify{background:var(--magenta)}
  .btn-signup{background:var(--violet)}
  .phone{position:absolute;left:727px;top:75px;width:354px;height:734px;border-radius:46px;background:linear-gradient(135deg,#f6f6f8,#cfcfd6 60%,#f0f0f3);padding:7px;box-shadow:0 8px 14px rgba(0,0,0,.12)}
  .screen{width:100%;height:100%;border-radius:40px;background:linear-gradient(180deg,#4a14b2 0%,#6a1aa8 45%,#b0288e 100%);position:relative;color:var(--white);text-align:center}
  .screen-brand{position:absolute;left:0;right:0;top:186px;font-weight:300;font-size:40px;letter-spacing:2px;line-height:1}
  .screen-slogan{position:absolute;left:30px;right:30px;top:260px;font-size:16.5px;line-height:32px;font-weight:400}
  .notify-field{position:absolute;left:34px;top:545px;width:278px;height:32px;border-radius:16px;background:var(--white);display:flex;align-items:center;justify-content:center;color:var(--magenta);font-size:11px;font-weight:500}
  .notify-field .bell{position:absolute;left:1px;top:1px;width:30px;height:30px;border-radius:50%;background:var(--violet);border:2px solid var(--magenta);display:flex;align-items:center;justify-content:center}
  .screen-note{position:absolute;left:38px;right:38px;top:604px;font-size:9.5px;line-height:19px}
  .dot{position:absolute;left:1128px;top:471px;width:14px;height:14px;border-radius:50%;background:#111}
  .footer{position:absolute;left:0;top:842px;width:1200px;height:60px;background:var(--footer);color:var(--white)}
  .copyright{position:absolute;left:111px;top:20px;font-size:13.5px}
  .social{position:absolute;left:961px;top:12px;display:flex;gap:9px}
  .social a{width:37px;height:37px;border-radius:50%;background:var(--magenta);display:flex;align-items:center;justify-content:center}
</style>
</head>
<body>
<main class="page">
  <svg class="backdrop" viewBox="0 0 1200 842" role="img" aria-label="Magenta backdrop with glowing open padlocks">
    <defs>
      <linearGradient id="band" x1="0" y1="0" x2="1" y2="1">
        <stop offset="0" stop-color="#b0268e"/>
        <stop offset="0.6" stop-color="#a82a8e"/>
        <stop offset="1" stop-color="#b22c90"/>
      </linearGradient>
      <linearGradient id="glow" x1="0" y1="0" x2="1" y2="0">
        <stop offset="0" stop-color="#ffffff" stop-opacity="0"/>
        <stop offset="1" stop-color="#f0d0ea" stop-opacity="0.8"/>
      </linearGradient>
      <radialGradient id="haze" cx="0.35" cy="0.55" r="0.5">
        <stop offset="0" stop-color="#dfeaf4" stop-opacity="0.7"/>
        <stop offset="1" stop-color="#ffffff" stop-opacity="0"/>
      </radialGradient>
    </defs>
    <polygon points="155,0 1200,0 1200,435 1080,518 728,450" fill="url(#band)"/>
    <polygon points="820,0 1200,0 1200,140 1000,210" fill="url(#glow)"/>
    <ellipse cx="320" cy="460" rx="330" ry="260" fill="url(#haze)"/>
  </svg>

  <div class="brand">KELVOLINK</div>

  <svg class="menu-icon" width="24" height="20" viewBox="0 0 24 20" aria-label="Menu">
    <g fill="#ffffff">
      <circle cx="2.5" cy="3" r="2.5"/><rect x="7" y="1" width="17" height="4" rx="2"/>
      <circle cx="2.5" cy="10" r="2.5"/><rect x="7" y="8" width="17" height="4" rx="2"/>
      <circle cx="2.5" cy="17" r="2.5"/><rect x="7" y="15" width="17" height="4" rx="2"/>
    </g>
  </svg>

  <h1 class="headline">
    <span class="l1">Unlocking</span>
    <span class="l2">The Power Of</span>
    <span class="l3">Meaningful</span>
    <span class="l4">Connections</span>
  </h1>

  <p class="intro">I must explain to you how all this mistaken idea of denouncing pleasure and praising pain was born and I will give you a complete account of the system, and expound the actual teachings.</p>

  <div class="actions">
    <a class="btn btn-notify">Notify Me</a>
    <a class="btn btn-signup">Sign Up</a>
  </div>

  <div class="phone">
    <div class="screen">
      <div class="screen-brand">KELVOLINK</div>
      <p class="screen-slogan">Unlocking the power of meaningful connections</p>
      <div class="notify-field">
        <span class="bell">
          <svg width="9" height="10" viewBox="0 0 9 10"><path d="M4.5 0.5c-1.7 0-2.8 1.3-2.8 3v2.3L0.6 7.4h7.8L7.3 5.8V3.5c0-1.7-1.1-3-2.8-3zM3.4 8.3a1.1 1.1 0 0 0 2.2 0z" fill="#fff"/></svg>
        </span>
        Notify Me
      </div>
      <p class="screen-note">Sed ut perspiciatis unde omnis iste natus error sit voluptatem accusantium doloremque laudantium, totam rem aperiam, eaque ipsa quae ab illo inventore veritatis</p>
    </div>
  </div>

  <span class="dot"></span>

  <footer class="footer">
    <p class="copyright">(C) Copyright 2024 | All Rights Reserved</p>
    <nav class="social" aria-label="Social links">
      <a aria-label="Email">
        <svg width="15" height="11" viewBox="0 0 15 11"><rect x="0.75" y="0.75" width="13.5" height="9.5" rx="1.5" fill="none" stroke="#fff" stroke-width="1.5"/><path d="M1 1.5l6.5 5 6.5-5" fill="none" stroke="#fff" stroke-width="1.5"/></svg>
      </a>
      <a aria-label="Chat">
        <svg width="15" height="14" viewBox="0 0 15 14"><path d="M2 1h11a1.5 1.5 0 0 1 1.5 1.5v6A1.5 1.5 0 0 1 13 10H6l-3.5 3V10H2A1.5 1.5 0 0 1 .5 8.5v-6A1.5 1.5 0 0 1 2 1z" fill="#fff"/></svg>
      </a>
      <a aria-label="Website">
        <svg width="15" height="15" viewBox="0 0 15 15"><circle cx="7.5" cy="7.5" r="6.5" fill="none" stroke="#fff" stroke-width="1.4"/><ellipse cx="7.5" cy="7.5" rx="2.8" ry="6.5" fill="none" stroke="#fff" stroke-width="1.2"/><path d="M1 7.5h13" stroke="#fff" stroke-width="1.2"/></svg>
      </a>
    </nav>
  </footer>
</main>
</body>
</html>
```